Harbor Crestline (Business Card Design)

Need business cards designed. Something modern, chic, and sleek. Mabye the back of the card should be the navy blue that is in the logo and then just the logo on the back.

Target Market(s)

Those in the hotel, office, and renovation industry

Contact Information for Business Card

1. Logo 2. Dorian Fenwick 3. CEO/Founder 4. Phone: (833) HarbCre / (833) 427-2731 5. Email: dorian@theharborcrestline.com 6. Website: www.theharborcrestline.com

Font styles to use
Other font styles liked:
• Look at the logo font and base the font for everything else off of that.

Colors
0054AA
0677BA
7BADD7
CADEEF
E8F1F8

Requirements
Must have
• Colors that are associated in the logo
Nice to have
• Sleek modern clean and chic design.

```html
<!DOCTYPE html>
<html lang="en">
<head>
<meta charset="UTF-8">
<title>Harbor Crestline — Business Card</title>
<link href="https://fonts.googleapis.com/css2?family=Montserrat:wght@600&family=Poppins:wght@400;600&display=swap" rel="stylesheet">
<style>
  :root {
    --navy: #0b1941;
    --gold: #d4a84b;
    --ink: #0f1630;
    --paper: #ffffff;
    --backdrop: #808080;
    --rule: #b9bcc4;
  }
  * { box-sizing: border-box; margin: 0; padding: 0; }
  html, body {
    width: 1093px; height: 1200px; overflow: hidden;
    background: var(--backdrop);
  }
  .card {
    position: absolute;
    left: 265px;
    width: 578px; height: 356px;
    border-radius: 28px;
  }
  .card--front { top: 226px; background: var(--paper); }
  .card--back  { top: 621px; background: var(--navy); }

  .wordmark {
    font-family: "Montserrat", sans-serif;
    font-weight: 600;
    letter-spacing: 0.08em;
    text-transform: uppercase;
    text-align: center;
    line-height: 1.15;
  }
  .wordmark__square {
    display: block;
    width: 10px; height: 10px;
    background: var(--gold);
    margin: 0 auto 14px;
  }
  .card--front .wordmark {
    position: absolute;
    left: 20px; width: 182px; top: 120px;
    color: var(--navy);
    font-size: 22px;
  }
  .divider {
    position: absolute;
    left: 221px; top: 74px;
    width: 1px; height: 209px;
    background: var(--rule);
  }
  .identity {
    position: absolute;
    left: 243px; top: 100px;
    font-family: "Poppins", sans-serif;
  }
  .identity__name {
    font-weight: 600; font-size: 22px; line-height: 1.1;
    color: var(--navy); letter-spacing: -0.01em;
  }
  .identity__title {
    font-size: 14px; color: var(--gold); margin-top: 3px;
  }
  .contact {
    position: absolute;
    left: 243px; top: 180px;
    list-style: none;
    font-family: "Poppins", sans-serif;
    font-size: 17px; color: var(--ink);
  }
  .contact li {
    display: flex; align-items: center; gap: 7px;
    height: 24.5px;
  }
  .contact svg { width: 16px; height: 16px; flex: none; fill: var(--navy); }

  .card--back .wordmark {
    position: absolute;
    left: 0; right: 0; top: 138px;
    color: var(--paper);
    font-size: 34px;
  }
</style>
</head>
<body>
  <section class="card card--front" aria-label="Card front">
    <div class="wordmark"><span class="wordmark__square"></span>Harbor<br>Crestline</div>
    <div class="divider"></div>
    <div class="identity">
      <h1 class="identity__name">DORIAN FENWICK</h1>
      <p class="identity__title">CEO/FOUNDER</p>
    </div>
    <ul class="contact">
      <li>
        <svg viewBox="0 0 24 24" aria-hidden="true"><path d="M6.6 10.8a15 15 0 0 0 6.6 6.6l2.2-2.2c.3-.3.7-.4 1-.2 1.1.4 2.3.6 3.6.6.6 0 1 .4 1 1V20c0 .6-.4 1-1 1A17 17 0 0 1 3 4c0-.6.4-1 1-1h3.5c.6 0 1 .4 1 1 0 1.3.2 2.5.6 3.6.1.3 0 .7-.2 1z"/></svg>
        (833) HarbCre / (833) 427-2731
      </li>
      <li>
        <svg viewBox="0 0 24 24" aria-hidden="true"><path d="M2 5h20v14H2zm2 2v.5l8 5 8-5V7zm0 2.8V17h16V9.8l-8 5z"/></svg>
        dorian@theharborcrestline.com
      </li>
      <li>
        <svg viewBox="0 0 24 24" aria-hidden="true"><path d="M12 2a10 10 0 1 0 0 20 10 10 0 0 0 0-20zm6.9 6h-2.9a15 15 0 0 0-1.3-3.6A8 8 0 0 1 18.9 8zM12 4c.8 1.2 1.5 2.5 1.9 4h-3.8c.4-1.5 1.1-2.8 1.9-4zM4.3 14a8 8 0 0 1 0-4h3.4a16 16 0 0 0 0 4zm.8 2h2.9c.3 1.3.8 2.5 1.3 3.6A8 8 0 0 1 5.1 16zM8 8H5.1a8 8 0 0 1 4.3-3.6C8.8 5.5 8.3 6.7 8 8zm4 12c-.8-1.2-1.5-2.5-1.9-4h3.8c-.4 1.5-1.1 2.8-1.9 4zm2.3-6H9.7a14 14 0 0 1 0-4h4.6a14 14 0 0 1 0 4zm.3 5.6c.5-1.1 1-2.3 1.3-3.6h2.9a8 8 0 0 1-4.2 3.6zm1.7-5.6a16 16 0 0 0 0-4h3.4a8 8 0 0 1 0 4z"/></svg>
        www.theharborcrestline.com
      </li>
    </ul>
  </section>

  <section class="card card--back" aria-label="Card back">
    <div class="wordmark"><span class="wordmark__square"></span>Harbor Crestline</div>
  </section>
</body>
</html>
```